Real Estate Business Card

On the front side I want to have my info, my brokerage info.
On the back side I want have my complany’s logo, website and Facebook link. I will provide all this once I select a design.

I would like to see Black background and gold text, Dark Blue and gold text and White and blue text designs

Font styles to use
Sans Serif
Script

```html
<!DOCTYPE html>
<html lang="en">
<head>
<meta charset="utf-8">
<title>Harbor Key Realty – Business Card</title>
<link rel="stylesheet" href="https://fonts.googleapis.com/css2?family=Cinzel:wght@500;600&family=Open+Sans:wght@400&display=swap">
<style>
  :root {
    --backdrop: #4b4b4d;
    --card-navy: #10305a;
    --gold: #e9c43c;
    --ink-light: #f2f2f2;
    --divider: rgba(255,255,255,0.18);
  }
  * { margin: 0; padding: 0; box-sizing: border-box; }
  html, body { width: 1200px; height: 802px; overflow: hidden; }
  body { background: var(--backdrop); position: relative; font-family: "Open Sans", sans-serif; }

  .card {
    position: absolute;
    top: 274px;
    width: 443px;
    height: 264px;
    background: var(--card-navy);
    box-shadow: 2px 3px 6px rgba(0,0,0,0.45);
  }
  .card--front { left: 136px; }
  .card--back { left: 624px; }

  .brand-name {
    position: absolute;
    font-family: "Cinzel", serif;
    font-weight: 600;
    color: var(--gold);
    text-align: center;
    white-space: nowrap;
    letter-spacing: 0.5px;
  }
  .card--front .brand-name {
    left: 20px; width: 190px; top: 122px;
    font-size: 22px; line-height: 26px;
  }
  .card--back .brand-name {
    left: 0; width: 100%; top: 120px;
    font-size: 30px; line-height: 36px;
  }

  .divider {
    position: absolute;
    left: 227px; top: 67px;
    width: 1px; height: 130px;
    background: var(--divider);
  }

  .contact-block { position: absolute; left: 241px; top: 64px; }
  .agent-name {
    font-family: "Cinzel", serif;
    font-weight: 600;
    color: var(--gold);
    font-size: 18px;
    line-height: 20px;
    letter-spacing: 0.3px;
    white-space: nowrap;
  }
  .agent-title { color: var(--ink-light); font-size: 13px; line-height: 16px; margin-bottom: 5px; }
  .contact-list { list-style: none; }
  .contact-list li {
    display: flex; align-items: center; gap: 5px;
    color: var(--ink-light); font-size: 12.5px; line-height: 16px;
    white-space: nowrap;
  }
  .contact-list svg { width: 10px; height: 10px; fill: var(--gold); flex: none; }
  .address { color: var(--ink-light); font-size: 12.5px; line-height: 15.5px; margin-top: 6px; }

  .social-link {
    position: absolute; left: 0; width: 100%; top: 214px;
    text-align: center; color: var(--ink-light); font-size: 11px;
  }
</style>
</head>
<body>
  <section class="card card--front" aria-label="Card front">
    <div class="brand-name">Harbor Key<br>Realty</div>
    <div class="divider"></div>
    <div class="contact-block">
      <div class="agent-name">DANIEL HARTWELL</div>
      <div class="agent-title">Managing Director</div>
      <ul class="contact-list">
        <li><svg viewBox="0 0 10 10" aria-hidden="true"><path d="M0 3.5C0 1.5 2 1 5 1s5 .5 5 2.5L8 4.5 7 3H3L2 4.5zM2 5h6l1 4H1z"/></svg>044-555 010 200</li>
        <li><svg viewBox="0 0 10 10" aria-hidden="true"><path d="M3 0h4a1 1 0 0 1 1 1v8a1 1 0 0 1-1 1H3a1 1 0 0 1-1-1V1a1 1 0 0 1 1-1zm.5 1.5v6h3v-6z"/></svg>044-555 010 201</li>
        <li><svg viewBox="0 0 10 10" aria-hidden="true"><path d="M2.5 0h5v3h-5zM0 3.5h10v4H8V10H2V7.5H0zM3 6v3h4V6z"/></svg>044-555 010 202</li>
        <li><svg viewBox="0 0 10 10" aria-hidden="true"><path d="M0 2h10v6H0zm1 1v.3l4 2.5 4-2.5V3z"/></svg>hello@harborkeyrealty.com</li>
        <li><svg viewBox="0 0 10 10" aria-hidden="true"><circle cx="5" cy="5" r="5"/></svg>www.harborkeyrealty.com</li>
      </ul>
      <p class="address">48 Lantern Quay Road<br>Westmere, 560218.</p>
    </div>
  </section>

  <section class="card card--back" aria-label="Card back">
    <div class="brand-name">Harbor Key Realty</div>
    <p class="social-link">social page: /harborkeyrealty</p>
  </section>
</body>
</html>
```